Popular Golf Club needs attractive brochure

We need a brochure that will attract golfers to come to the Kestrel River area and the Brindlewood Golf Club for their golfing holiday. It also needs to address the availability of a function area and corporate functions in the clubhouse and corporate golf days on the course as well.
It will highlight our direct phone contact numbers and website as well.
We are a 36 Hole Championship Golf Course on the Kestrel River border of NSW and Victoria. 3 hours easy freeway drive from Melbourne. Over 300 sunny days every year. Fabulous golf weather all year round. Raincheck guarantee (if it rains we will give you free golf on you next visit).
The area is a golf and watersport playground. Sandy beaches, the mighty Kesterl River, home of the giant Kestrel Perch, fishing, camping, boating and golf all on your doorstep.
We can arrange Golf packages for individuals and groups including 3 and 4 star accommodation available all year round.

Target Market(s)

Golfers looking for holidays

Industry/Entity Type

Accommodation

Requirements
Must have
• Branding bar and logo. Colours signifying sun, grass and river.
Nice to have
• Smiling happy golfers, particularly more senior age group. Map of location and proximity to Melbourne. Photos of the course. some attached, many more available.

```html
<!DOCTYPE html>
<html lang="en">
<head>
<meta charset="utf-8">
<title>Brindlewood Golf Club – Brochure</title>
<link rel="stylesheet" href="https://fonts.googleapis.com/css2?family=Open+Sans:wght@400;600;700&family=Arimo:wght@400&display=swap">
<style>
:root{
  --grass:#8cc63f;
  --river:#4cb3c9;
  --sun:#f6c81a;
  --ink:#333333;
  --paper:#ffffff;
  --fold:#d6d6d6;
  --backdrop:#e9e6e1;
}
*{box-sizing:border-box;margin:0;padding:0}
html,body{width:1200px;height:969px;overflow:hidden;background:var(--backdrop)}
.brochure{position:absolute;left:30px;top:42px;width:1140px;height:885px;background:var(--paper);overflow:hidden;box-shadow:0 4px 18px rgba(0,0,0,.18);font-family:"Open Sans",Arial,sans-serif}
.panel{position:absolute;top:0;height:100%}
.panel--left{left:0;width:380px}
.panel--middle{left:380px;width:380px;border-left:1px solid var(--fold);border-right:1px solid var(--fold)}
.panel--right{left:760px;width:380px}
.photo{position:absolute;display:block}

/* left */
.intro-badge{position:absolute;left:8px;top:50px;width:22px;height:22px;border-radius:50%;background:var(--sun)}
.intro-title{position:absolute;left:58px;top:43px;width:277px;height:36px;background:var(--grass);border-radius:0 10px 10px 0;color:#fff;font-weight:700;font-size:19px;line-height:36px;padding-left:15px}
.intro-copy{position:absolute;left:28px;top:122px;width:322px;font-family:"Arimo",Arial,sans-serif;font-size:13px;line-height:36px;color:var(--ink);text-indent:34px}
.course-photo{left:0;top:592px;width:380px;height:203px;background:linear-gradient(180deg,#8fb56e 0%,#5e8d3a 45%,#7cae45 100%)}

/* middle */
.shop-frame{position:absolute;left:94px;top:53px;width:183px;height:142px;border:4px solid var(--river)}
.shop-photo{left:0;top:0;width:100%;height:100%;background:linear-gradient(180deg,#c9ced2 0%,#b5bfb8 45%,#5f9a3c 62%,#4d8a33 100%)}
.shop-lines{position:absolute;left:84px;top:44px;width:210px;height:175px}
.shop-caption{position:absolute;left:133px;top:201px;font-size:12px;font-weight:700;color:var(--river);white-space:nowrap}
.club-name{position:absolute;left:0;width:100%;display:flex;align-items:center;justify-content:center;color:var(--ink);text-transform:uppercase;font-weight:400}
.club-name__dot{border-radius:50%;background:var(--sun);flex:none}
.club-name__main{display:block;line-height:1.1}
.club-name__sub{display:block;line-height:1.4}
.club-name--middle{top:248px;gap:12px}
.club-name--middle .club-name__dot{width:60px;height:60px}
.club-name--middle .club-name__main{font-size:21px;letter-spacing:3px}
.club-name--middle .club-name__sub{font-size:11px;letter-spacing:7px}
.contact{position:absolute;left:0;width:100%;top:340px;text-align:center;font-size:14.5px;line-height:19.5px;color:var(--ink);font-style:normal}
.contact__title{font-size:18px;font-weight:700;color:var(--sun);line-height:28px}
.contact__label{font-weight:700;color:var(--sun)}
.contact__label--blue{color:var(--river)}
.contact__link{color:var(--river)}
.contact__row--gap{margin-top:8px}
.contact__row--web{margin-top:4px}
.location-map{left:10px;top:534px;width:363px;height:241px;background:linear-gradient(135deg,#e6e6e3 0%,#dfe3d8 55%,#cfe0bf 100%)}

/* right */
.top-stripe{position:absolute;left:0;width:380px;height:6px}
.top-stripe--sun{top:0;background:var(--sun)}
.top-stripe--river{top:11px;background:var(--river)}
.club-name--right{top:98px;gap:14px}
.club-name--right .club-name__dot{width:66px;height:66px}
.club-name--right .club-name__main{font-size:26px;letter-spacing:4px}
.club-name--right .club-name__sub{font-size:15px;letter-spacing:9px}
.gallery-1{left:50px;top:243px;width:134px;height:103px;background:linear-gradient(160deg,#6b5a4a,#b9a58c)}
.gallery-2{left:191px;top:237px;width:166px;height:109px;background:linear-gradient(180deg,#aab4b8 0%,#4f6a3c 60%,#3f5f2e 100%)}
.gallery-3{left:17px;top:353px;width:167px;height:111px;background:linear-gradient(180deg,#8a5a3c,#5b4a5c)}
.gallery-4{left:191px;top:353px;width:142px;height:111px;background:linear-gradient(180deg,#c5cdd4 0%,#7e9a6a 55%,#5f8e3e 100%)}
.tagline{position:absolute;left:0;width:100%;top:512px;text-align:center;font-weight:600}
.tagline__line{display:block}
.tagline__line--green{color:var(--grass);font-size:31px;line-height:36px}
.tagline__line--yellow{color:var(--sun);font-size:28px;line-height:36px}
.tagline__line--blue{color:var(--river);font-size:38px;line-height:34px}
.quick-contact{position:absolute;left:0;width:100%;top:647px;text-align:center;color:var(--river);font-size:19px;line-height:32px}
.quick-contact strong{font-weight:700}

/* footer band */
.band{position:absolute;left:0;width:1140px}
.band--river{top:772px;height:8px;background:var(--river)}
.band--sun{top:784px;height:8px;background:var(--sun)}
.band--grass{top:795px;height:90px;background:var(--grass)}
</style>
</head>
<body>
<main class="brochure">
  <section class="panel panel--left">
    <span class="intro-badge"></span>
    <h2 class="intro-title">You Can Be Happy!</h2>
    <p class="intro-copy">The secret is out! Along the Mighty Kestrel, Brindlewood Golf Course is maintained at the highest levels of excellence unsurpassed on the River. This magnificent 36 hole championship sand-belt course offers a challenge to golfers of all levels and hosts the annual Southern Pro Trainee Championships. With in excess of 300 days of sunshine each year, the region boasts more sunny weather than the Gold Coast with two superb golf courses (President’s and Captain’s) that are suitable to play all year round.</p>
    <div class="photo course-photo" role="img" aria-label="Photo of a fairway and green lined with trees"></div>
  </section>

  <section class="panel panel--middle">
    <svg class="shop-lines" viewBox="0 0 210 175" aria-hidden="true">
      <g stroke="var(--grass)" stroke-width="1.5" fill="none">
        <line x1="0" y1="4" x2="210" y2="4"/><line x1="0" y1="9" x2="210" y2="9"/>
        <line x1="200" y1="0" x2="200" y2="175"/><line x1="205" y1="0" x2="205" y2="175"/>
      </g>
    </svg>
    <div class="shop-frame">
      <div class="photo shop-photo" role="img" aria-label="Photo of the club shop putting green"></div>
    </div>
    <p class="shop-caption">Brindlewood Golf club shop</p>
    <div class="club-name club-name--middle"><span class="club-name__dot"></span><span><span class="club-name__main">Brindlewood</span><span class="club-name__sub">Golf Club</span></span></div>
    <address class="contact">
      <div class="contact__title">Contact us</div>
      <div>Brindlewood Golf Club</div>
      <div>Corella Rd, Wrenford N.S.W. 2790</div>
      <div class="contact__row--gap"><span class="contact__label">Phone :</span> 03 5550 0142</div>
      <div><span class="contact__label">Fax :</span> 03 5550 0143</div>
      <div><span class="contact__label">FREE CALL :</span> 1800 555 019</div>
      <div><span class="contact__label contact__label--blue">E-mail :</span> admin@brindlewoodgolf.com.au</div>
      <div class="contact__row--web"><span class="contact__label contact__label--blue">Website :</span> <span class="contact__link">www.brindlewoodgolf.com.au</span></div>
    </address>
    <div class="photo location-map" role="img" aria-label="Street map showing the golf club location in Wrenford"></div>
  </section>

  <section class="panel panel--right">
    <span class="top-stripe top-stripe--sun"></span>
    <span class="top-stripe top-stripe--river"></span>
    <div class="club-name club-name--right"><span class="club-name__dot"></span><span><span class="club-name__main">Brindlewood</span><span class="club-name__sub">Golf Club</span></span></div>
    <div class="photo gallery-1" role="img" aria-label="Photo of trophies on display"></div>
    <div class="photo gallery-2" role="img" aria-label="Photo of a group of golfers on the course"></div>
    <div class="photo gallery-3" role="img" aria-label="Photo of a corporate function in the clubhouse"></div>
    <div class="photo gallery-4" role="img" aria-label="Photo of a golfer teeing off"></div>
    <h1 class="tagline">
      <span class="tagline__line tagline__line--green">A great golf</span>
      <span class="tagline__line tagline__line--yellow">course is</span>
      <span class="tagline__line tagline__line--blue">just the beginning</span>
    </h1>
    <div class="quick-contact">
      <div><strong>Phone :</strong> 03 5550 0142</div>
      <div>www.brindlewoodgolf.com.au</div>
    </div>
  </section>

  <span class="band band--river"></span>
  <span class="band band--sun"></span>
  <span class="band band--grass"></span>
</main>
</body>
</html>
```